Pellham Grove Trust - New Website Designed

I need a site that looks like this http://www.quorlandgiving.org for boat donations. So please replace the cars with boats.

```html
<!DOCTYPE html>
<html lang="en">
<head>
<meta charset="utf-8">
<title>Pellham Grove Trust — Donate Your Boat</title>
<link href="https://fonts.googleapis.com/css2?family=Open+Sans:wght@400;600;700;800&display=swap" rel="stylesheet">
<style>
:root{
  --canvas:#dde9f7;
  --ink:#222;
  --dark:#2b2b2b;
  --nav:#1a7bc4;
  --red:#8e1b1b;
  --red-top:#7a1414;
  --royal:#2e4fb0;
  --royal-deep:#2a48a6;
  --navy:#0f4a72;
  --light:#f2f2f2;
  --white:#fff;
  --line:#c9c9c9;
  --title-blue:#2a4fb5;
}
*{box-sizing:border-box;margin:0;padding:0}
html,body{width:1200px;height:2400px;overflow:hidden}
body{background:var(--canvas);font-family:"Open Sans",Arial,sans-serif;color:var(--ink)}
.page{position:absolute;left:80px;top:0;width:1040px;height:2400px;background:var(--white)}
.abs{position:absolute}

/* header */
.topbar{left:0;top:0;width:669px;height:93px;background:var(--dark)}
.brand{left:139px;top:26px;font-size:30px;font-weight:600;color:var(--white);white-space:nowrap}
.nav{left:0;top:93px;width:669px;height:38px;background:var(--nav);display:flex}
.nav a{flex:1;color:var(--white);text-decoration:none;font-size:12px;font-weight:600;text-align:center;line-height:38px;border-right:1px solid rgba(255,255,255,.25)}
.nav a:last-child{border-right:0}
.hero-photo{left:0;top:131px;width:1040px;height:421px;background:linear-gradient(135deg,#5b7fae 0%,#8eaad0 45%,#5d6d55 70%,#3e5f8f 100%)}

/* donate panel */
.panel{left:669px;top:0;width:371px;height:552px;background:rgba(142,27,27,.93)}
.panel-top{left:669px;top:0;width:371px;height:100px;background:var(--red-top)}
.callbox{display:flex;align-items:center;gap:16px;color:var(--white)}
.callbox .ring{width:58px;height:58px;border:2px solid var(--white);border-radius:50%;display:flex;align-items:center;justify-content:center;flex:none}
.callbox small{display:block;font-size:11px;font-weight:700;letter-spacing:.3px}
.callbox strong{display:block;font-size:27px;font-weight:700;line-height:1.1}
.panel .callbox{position:absolute;left:34px;top:20px}
.form-title{left:669px;top:108px;width:371px;text-align:center;color:var(--white);font-size:18px;font-weight:700}
.form-sub{left:669px;top:136px;width:371px;text-align:center;color:var(--white);font-size:14px}
.field{height:37px;background:var(--white);border-radius:4px;font-size:11px;color:#777;padding-left:14px;line-height:37px;display:flex;justify-content:space-between;padding-right:14px}
.cta{left:685px;top:478px;width:320px;height:47px;background:var(--title-blue);border-radius:4px;color:var(--white);font-weight:700;font-size:17px;text-align:center;line-height:47px}

/* benefit band */
.band{left:0;top:552px;width:1040px;height:149px;background:var(--royal)}
.band-lead{left:0;top:552px;width:310px;height:149px;background:var(--dark);clip-path:polygon(0 0,100% 0,100% 100%,94% 100%,74% 100%,60% 100%,0 100%);}
.band-slant{left:240px;top:552px;width:80px;height:149px;background:var(--dark);clip-path:polygon(0 0,40% 0,0 100%)}
.band-lead-wrap{left:0;top:552px;width:300px;height:149px;background:var(--dark);clip-path:polygon(0 0,100% 0,86% 100%,0 100%)}
.band-kicker{left:33px;top:592px;color:var(--white);font-size:17px;font-weight:600}
.band-head{left:33px;top:614px;color:var(--white);font-size:41px;font-weight:600;letter-spacing:1px}
.perk{width:140px;text-align:center;color:var(--white);font-size:13px;line-height:1.35}
.perk svg{display:block;margin:0 auto 10px}

/* how to donate */
.how{left:0;top:701px;width:1040px;height:307px;background:var(--light)}
.sec-title{width:1040px;text-align:center;font-size:18px;font-weight:700;color:var(--title-blue)}
.step{display:flex;gap:16px;align-items:center;width:300px}
.step .circ{width:88px;height:88px;border:1.5px solid var(--royal);border-radius:50%;background:var(--white);display:flex;align-items:center;justify-content:center;flex:none}
.step h3{font-size:12px;font-weight:700;color:var(--ink);margin-bottom:6px}
.step p{font-size:10px;line-height:1.45;color:#444}

/* why */
.why{left:0;top:1008px;width:1040px;height:528px;background:var(--navy)}
.why .sec-title{color:var(--white)}
.reason{width:400px;display:flex;gap:18px;color:var(--white)}
.reason svg{flex:none}
.reason h3{font-size:13px;font-weight:700;margin-bottom:6px}
.reason p{font-size:12.5px;line-height:1.6;color:#e3ecf4}

/* faq */
.faq-photo{left:51px;top:1654px;width:472px;height:372px;background:linear-gradient(160deg,#b8202e 0%,#e9e6e6 35%,#1d3a78 60%,#14305f 100%)}
.faq-item{left:557px;width:432px;height:45px;border:1px solid var(--line);display:flex;align-items:center;gap:16px;padding-left:16px;font-size:12px;color:#333}
.faq-item .plus{width:16px;height:16px;border-radius:50%;background:#111;position:relative;flex:none}
.faq-item .plus::before,.faq-item .plus::after{content:"";position:absolute;background:var(--white);left:4px;top:7px;width:8px;height:2px}
.faq-item .plus::after{transform:rotate(90deg)}

/* footer */
.footer{left:0;top:2104px;width:1040px;height:296px;background:var(--royal)}
.foot-brand{left:59px;top:2160px;font-size:28px;font-weight:600;color:var(--white);white-space:nowrap}
.foot-about{left:59px;top:2222px;width:370px;font-size:12px;line-height:1.7;color:#e6ebf8}
.foot-menu{left:507px;top:2168px;color:var(--white);font-size:12px}
.foot-menu h4{font-size:12px;font-weight:700;margin-bottom:26px}
.foot-menu li{list-style:none;line-height:1.65}
.foot-call{left:706px;top:2168px}
.copyright{left:734px;top:2315px;color:var(--white);font-size:11px}
</style>
</head>
<body>
<div class="page">

  <div class="abs hero-photo" role="img" aria-label="Photo of a veteran in uniform hugging a young girl holding a small flag, with motor yachts against a blue sky"></div>

  <header>
    <div class="abs topbar"></div>
    <div class="abs brand">Pellham Grove Trust</div>
    <nav class="abs nav">
      <a href="#">HOME</a><a href="#">HOW TO DONATE</a><a href="#">WHY DONATE</a><a href="#">ABOUT US</a>
    </nav>
  </header>

  <section>
    <div class="abs panel"></div>
    <div class="abs panel-top"></div>
    <div class="abs" style="left:669px;top:0;width:371px;height:100px">
      <div class="callbox" style="position:absolute;left:34px;top:20px">
        <span class="ring"><svg width="28" height="28" viewBox="0 0 24 24" fill="none" stroke="#fff" stroke-width="1.6"><path d="M5 3h4l2 5-2.5 1.5a11 11 0 0 0 6 6L16 13l5 2v4a2 2 0 0 1-2 2A17 17 0 0 1 3 5a2 2 0 0 1 2-2z"/><path d="M15 3a6 6 0 0 1 6 6M15 7a2 2 0 0 1 2 2"/></svg></span>
        <span><small>WE NEED YOUR HELP</small><strong>1-800-555-0142</strong><small>7 DAYS A WEEK</small></span>
      </div>
    </div>
    <div class="abs form-title">DONATE YOUR BOAT ONLINE</div>
    <div class="abs form-sub">Full Tax Deduction - Running or Not</div>
    <div class="abs field" style="left:685px;top:187px;width:153px">First Name</div>
    <div class="abs field" style="left:851px;top:187px;width:154px">Last Name</div>
    <div class="abs field" style="left:685px;top:235px;width:320px">Phone No.</div>
    <div class="abs field" style="left:685px;top:283px;width:320px">E mail Address</div>
    <div class="abs field" style="left:685px;top:333px;width:320px">Zip Code</div>
    <div class="abs field" style="left:685px;top:381px;width:153px"><span>Year of car</span><span>&#8964;</span></div>
    <div class="abs field" style="left:851px;top:381px;width:154px"><span>Choose Make</span><span>&#8964;</span></div>
    <div class="abs field" style="left:685px;top:430px;width:320px">Vehicle Model</div>
    <div class="abs cta">CLICK HERE TO DONATE NOW</div>
  </section>

  <section>
    <div class="abs band"></div>
    <div class="abs band-lead-wrap"></div>
    <div class="abs band-kicker">DONATE YOUR BOAT TO</div>
    <div class="abs band-head">VETERANS</div>
    <div class="abs perk" style="left:303px;top:580px"><svg width="34" height="38" viewBox="0 0 24 28" fill="none" stroke="#fff" stroke-width="1.5"><path d="M16 6h-6a3 3 0 0 0 0 6h4a3 3 0 0 1 0 6H7M12 2v24M4 24 20 4"/></svg>You have<br>no costs</div>
    <div class="abs perk" style="left:416px;top:580px"><svg width="44" height="38" viewBox="0 0 32 26" fill="none" stroke="#fff" stroke-width="1.5"><path d="M2 18V10h10l4 4h6V8l6-6M12 10v8M2 18h28v-4h-8"/><circle cx="8" cy="21" r="3"/><circle cx="24" cy="21" r="3"/></svg>Free towing,<br>running or not.</div>
    <div class="abs perk" style="left:572px;top:580px"><svg width="34" height="38" viewBox="0 0 24 28" fill="none" stroke="#fff" stroke-width="1.5"><rect x="3" y="2" width="18" height="24" rx="1"/><path d="M7 8h6M7 12h6M7 16h6M7 20h6M17 9v8"/></svg>We issue you an<br>IRS tax receipt.</div>
    <div class="abs perk" style="left:720px;top:580px"><svg width="34" height="38" viewBox="0 0 24 28" fill="#fff"><path d="M3 2h12l6 6v18H3z"/><path d="M7 13h10M7 17h10M7 21h7" stroke="#2e4fb0" stroke-width="1.5"/></svg>We take care of<br>all paperwork.</div>
    <div class="abs perk" style="left:864px;top:580px"><svg width="34" height="38" viewBox="0 0 24 28" fill="none" stroke="#fff" stroke-width="1.5"><rect x="3" y="3" width="18" height="23"/><path d="M3 3l2-2 2 2 2-2 2 2 2-2 2 2 2-2 2 2 2-2M7 10h10M7 14h10M7 18h10M7 22h6"/></svg>we take care of<br>DMV &amp; Smog issues.</div>
  </section>

  <section>
    <div class="abs how"></div>
    <h2 class="abs sec-title" style="left:0;top:762px">HOW TO DONATE</h2>
    <div class="abs step" style="left:52px;top:852px">
      <span class="circ"><svg width="40" height="40" viewBox="0 0 24 24" fill="none" stroke="#2e4fb0" stroke-width="1.4"><path d="M5 3h4l2 5-2.5 1.5a11 11 0 0 0 6 6L16 13l5 2v4a2 2 0 0 1-2 2A17 17 0 0 1 3 5a2 2 0 0 1 2-2z"/><path d="M15 3a6 6 0 0 1 6 6M15 7a2 2 0 0 1 2 2"/></svg></span>
      <div><h3>CALL US AT 1-800-555-0142 OR<br>FILL OUT THE ONLINE FORM</h3><p>Lorem Ipsum is simply dummy text of<br>the printing and typesetting .</p></div>
    </div>
    <div class="abs step" style="left:385px;top:852px">
      <span class="circ"><svg width="44" height="38" viewBox="0 0 32 26" fill="none" stroke="#2e4fb0" stroke-width="1.5"><path d="M2 18V10h10l4 4h6V8l6-6M12 10v8M2 18h28v-4h-8"/><circle cx="8" cy="21" r="3"/><circle cx="24" cy="21" r="3"/></svg></span>
      <div><h3>WE TOW THE BOAT</h3><p>Lorem Ipsum is simply dummy text of<br>the printing and typesetting .</p></div>
    </div>
    <div class="abs step" style="left:708px;top:852px">
      <span class="circ"><svg width="38" height="38" viewBox="0 0 24 24" fill="none" stroke="#2e4fb0" stroke-width="1.4"><rect x="3" y="3" width="15" height="19"/><path d="M6 8h9M6 12h9M6 16h5M20 6l-6 11-1 3 2-2 6-11z"/></svg></span>
      <div><h3>TAX WRITE-OFF</h3><p>Lorem Ipsum is simply dummy text of<br>the printing and typesetting .</p></div>
    </div>
  </section>

  <section>
    <div class="abs why"></div>
    <h2 class="abs sec-title" style="left:0;top:1058px">WHY DONATE YOUR BOAT TO US</h2>
    <div class="abs reason" style="left:58px;top:1144px">
      <svg width="52" height="50" viewBox="0 0 26 24" fill="none" stroke="#fff" stroke-width="1.5"><path d="M4 4h3l2 4-2 1.5a9 9 0 0 0 5 5L14 13l4 2v3a2 2 0 0 1-2 2A14 14 0 0 1 2 6a2 2 0 0 1 2-2z"/><text x="14" y="10" fill="#fff" stroke="none" font-size="8" font-weight="700" font-family="Open Sans,sans-serif">24</text></svg>
      <div><h3>CALL 24/7 SUPPORT</h3><p>Lorem Ipsum is simply dummy text of the printing<br>and typesetting .</p></div>
    </div>
    <div class="abs reason" style="left:550px;top:1140px">
      <svg width="72" height="40" viewBox="0 0 36 20" fill="none" stroke="#fff" stroke-width="1.5"><path d="M2 13h32l-5 4H7zM8 13l4-5h12l4 5M14 8l2-3h5"/><path d="M2 19c3-2 5 2 8 0s5 2 8 0 5 2 8 0 5 2 8 0"/></svg>
      <div><h3>All Boats Accepted</h3><p>Lorem Ipsum is simply dummy text of the printing and<br>typesetting .</p></div>
    </div>
    <div class="abs reason" style="left:58px;top:1262px">
      <svg width="52" height="46" viewBox="0 0 32 26" fill="none" stroke="#fff" stroke-width="1.7"><path d="M2 18V10h10l4 4h6V8l6-6M12 10v8M2 18h28v-4h-8"/><circle cx="8" cy="21" r="3"/><circle cx="24" cy="21" r="3"/></svg>
      <div><h3>Free Local Towing to You</h3><p>Lorem Ipsum is simply dummy text of the printing and<br>typesetting .</p></div>
    </div>
    <div class="abs reason" style="left:566px;top:1262px">
      <svg width="56" height="52" viewBox="0 0 24 24" fill="#fff"><rect x="9" y="2" width="11" height="8" rx="1"/><path d="M3 12h10l3 3v7H5z"/></svg>
      <div><h3>Income Tax Deduction</h3><p>Lorem Ipsum is simply dummy text of the printing and<br>typesetting .</p></div>
    </div>
    <div class="abs reason" style="left:62px;top:1390px">
      <svg width="48" height="50" viewBox="0 0 24 26" fill="none" stroke="#fff" stroke-width="1.5"><rect x="3" y="5" width="15" height="19"/><path d="M7 2h14v19M6 10h9M6 14h9M6 18h9"/></svg>
      <div><h3>No Paperwork Hassles</h3><p>Lorem Ipsum is simply dummy text of the printing and<br>typesetting .</p></div>
    </div>
    <div class="abs reason" style="left:558px;top:1390px">
      <svg width="64" height="56" viewBox="0 0 32 28"><polygon fill="#fff" points="16,1 19,5 24,3 25,8 30,9 28,14 31,18 26,20 26,25 21,24 18,28 15,25 10,27 9,22 4,21 5,16 1,12 6,10 6,5 11,5 13,1"/><text x="16" y="17" fill="#0f4a72" font-size="7" font-weight="800" text-anchor="middle" font-family="Open Sans,sans-serif" transform="rotate(-12 16 15)">FREE</text></svg>
      <div><h3>Schedule a Free Pickup</h3><p>Lorem Ipsum is simply dummy text of the printing and<br>typesetting .</p></div>
    </div>
  </section>

  <section>
    <h2 class="abs sec-title" style="left:0;top:1590px">FAQ</h2>
    <div class="abs faq-photo" role="img" aria-label="Waving stars and stripes flag above a white motor yacht on a dark blue star field"></div>
    <div class="abs faq-item" style="top:1654px"><span class="plus"></span>Lorem Ipsum is simply dummy text of the printing ?</div>
    <div class="abs faq-item" style="top:1709px"><span class="plus"></span>It is a long established fact that a reader</div>
    <div class="abs faq-item" style="top:1765px"><span class="plus"></span>All the Lorem Ipsum generators on the Internet</div>
    <div class="abs faq-item" style="top:1819px"><span class="plus"></span>The standard chunk of Lorem Ipsum used</div>
    <div class="abs faq-item" style="top:1874px"><span class="plus"></span>The standard chunk of Lorem Ipsum used</div>
    <div class="abs faq-item" style="top:1925px"><span class="plus"></span>The standard chunk of Lorem Ipsum used</div>
    <div class="abs faq-item" style="top:1981px"><span class="plus"></span>The standard chunk of Lorem Ipsum used</div>
  </section>

  <footer>
    <div class="abs footer"></div>
    <div class="abs foot-brand">Pellham Grove Trust</div>
    <p class="abs foot-about">There are many variations of passages of Lorem Ipsum available, but the majority have suffered alteration in some form, by injected humour, or randomised words which don't look even slightly believable. If you are going to use a passage of Lorem Ipsum, you need to be sure there isn't anything</p>
    <div class="abs foot-menu"><h4>MENU</h4><ul><li>HOW TO DONATE</li><li>WHY DONATE</li><li>FAQ</li><li>ABOUT</li></ul></div>
    <div class="abs foot-call">
      <div class="callbox">
        <span class="ring"><svg width="28" height="28" viewBox="0 0 24 24" fill="none" stroke="#fff" stroke-width="1.6"><path d="M5 3h4l2 5-2.5 1.5a11 11 0 0 0 6 6L16 13l5 2v4a2 2 0 0 1-2 2A17 17 0 0 1 3 5a2 2 0 0 1 2-2z"/><path d="M15 3a6 6 0 0 1 6 6M15 7a2 2 0 0 1 2 2"/></svg></span>
        <span><small>WE NEED YOUR HELP</small><strong>1-800-555-0142</strong><small>7 DAYS A WEEK</small></span>
      </div>
    </div>
    <div class="abs copyright">Copyrights @ 2017 All Rights Reserved</div>
  </footer>

</div>
</body>
</html>
```